Spring Detox sale graphics for social media

You MUST read the Brief in the WORD document and follow the instructions there. I want to create 10 social media graphics (new Instagram size 4:5 (1080 x 1350 pixels) focusing on our Mother’s Day Spring Detox Sale graphics, using any of the pics attached. Use the attached pics, NO RANDOM STOCK PHOTOGRAPHY. For the color scheme of the graphics, they should all be complementary to the product colors or feel like Spring time.

Target Market(s)

primarily women

Requirements
Must have
• the photos and text attached

```html
<!DOCTYPE html>
<html lang="en">
<head>
<meta charset="utf-8">
<title>Mother's Day Spring Detox Sale – Social Tiles</title>
<link rel="stylesheet" href="https://fonts.googleapis.com/css2?family=Anton&family=Archivo+Black&family=Bebas+Neue&family=Fredoka:wght@600;700&family=Kaushan+Script&family=Montserrat:ital,wght@0,600;1,800;1,900&family=Permanent+Marker&display=swap">
<style>
:root{
  --plum:#8f2160;
  --plum-deep:#7a2657;
  --wine:#7b3460;
  --pink:#f2a7d0;
  --pink-mid:#d35c9e;
  --blush:#fcecf5;
  --white:#ffffff;
  --bottle:#ece7ea;
}
*{margin:0;padding:0;box-sizing:border-box}
html,body{width:1200px;height:608px;overflow:hidden;background:var(--white)}
.board{position:relative;width:1200px;height:608px}
.tile{position:absolute;width:224px;height:280px;overflow:hidden;background:var(--plum)}
.tile--blush{background:var(--blush)}
.tile--fade{background:linear-gradient(180deg,var(--plum) 0%,var(--plum) 45%,#c4639a 100%)}
.t{position:absolute;left:0;right:0;text-align:center;line-height:1;white-space:nowrap}
.script{font-family:"Kaushan Script",cursive}
.bebas{font-family:"Bebas Neue",sans-serif}
.anton{font-family:"Anton",sans-serif}
.archivo{font-family:"Archivo Black",sans-serif}
.round{font-family:"Fredoka",sans-serif;font-weight:700}
.italic{font-family:"Montserrat",sans-serif;font-style:italic;font-weight:900;letter-spacing:-1px}
.brush{font-family:"Permanent Marker",cursive}
.spaced{font-family:"Montserrat",sans-serif;font-weight:600;letter-spacing:4px}
.photo{position:absolute;border-radius:6px;background:linear-gradient(180deg,#f7f3f5,var(--bottle))}
.white-curve{position:absolute;left:0;right:0;bottom:0;background:var(--white)}
.c-white{color:var(--white)} .c-pink{color:var(--pink)} .c-mid{color:var(--pink-mid)}
.c-plum{color:var(--plum)} .c-wine{color:var(--wine)}
</style>
</head>
<body>
<main class="board">

  <!-- Tile 1 -->
  <section class="tile" style="left:27px;top:21px">
    <svg class="white-curve" width="224" height="90" viewBox="0 0 224 90" style="height:90px"><path d="M0 28 Q112 -8 224 28 V90 H0Z" fill="#fff"/></svg>
    <p class="t script c-white" style="top:18px;font-size:28px">Mother's Day</p>
    <p class="t anton c-pink" style="top:44px;font-size:62px;letter-spacing:-1px">SPRING</p>
    <p class="t bebas c-white" style="top:110px;font-size:50px">DETOX SALE</p>
    <p class="t round c-pink" style="top:152px;font-size:17px">25% Off Everything!</p>
    <div class="photo" role="img" aria-label="Four supplement bottles in a row" style="left:20px;top:176px;width:186px;height:100px"></div>
  </section>

  <!-- Tile 2 -->
  <section class="tile" style="left:258px;top:21px">
    <p class="t bebas c-white" style="top:28px;font-size:66px">25% OFF</p>
    <p class="t script c-white" style="top:82px;font-size:32px">Mother's Day</p>
    <div style="position:absolute;left:23px;top:129px;width:118px;height:120px;background:#f8dcea;border-radius:4px"></div>
    <p class="script c-mid" style="position:absolute;left:38px;top:130px;font-size:30px;line-height:1">Spring</p>
    <p class="bebas c-wine" style="position:absolute;left:38px;top:164px;font-size:44px;line-height:1">DETOX</p>
    <p class="bebas c-mid" style="position:absolute;left:38px;top:203px;font-size:44px;line-height:1">SALE</p>
    <div class="photo" role="img" aria-label="Liver supplement bottle" style="left:128px;top:123px;width:77px;height:140px"></div>
  </section>

  <!-- Tile 3 -->
  <section class="tile tile--blush" style="left:488px;top:21px">
    <p class="t archivo c-mid" style="top:27px;font-size:29px">25% OFF</p>
    <p class="t bebas c-wine" style="top:55px;font-size:37px">ALL SUPPLEMENTS</p>
    <p class="t anton c-wine" style="top:78px;font-size:52px">SPRING</p>
    <p class="t archivo c-mid" style="top:128px;font-size:46px">DETOX</p>
    <p class="t anton c-wine" style="top:156px;font-size:116px;letter-spacing:-2px">SALE</p>
    <div class="photo" role="img" aria-label="Small supplement bottle" style="left:52px;top:218px;width:24px;height:42px"></div>
  </section>

  <!-- Tile 4 -->
  <section class="tile tile--fade" style="left:718px;top:21px">
    <p class="t italic c-white" style="top:20px;font-size:26px">25% OFF</p>
    <p class="t brush c-white" style="top:44px;font-size:50px">SPRING</p>
    <p class="t italic c-white" style="top:96px;font-size:25px">Detox Sale</p>
    <div class="photo" role="img" aria-label="Four supplement bottles grouped together" style="left:38px;top:128px;width:150px;height:86px"></div>
    <p class="t italic c-white" style="top:212px;font-size:22px">Spring Reset.</p>
    <p class="t italic c-white" style="top:236px;font-size:22px">Summer Ready</p>
  </section>

  <!-- Tile 5 -->
  <section class="tile" style="left:948px;top:21px">
    <p class="anton" style="position:absolute;left:22px;top:22px;font-size:118px;line-height:1;color:#f0e6ec" role="img" aria-label="Large 25 filled with a supplement bottle photo">25</p>
    <p class="bebas c-white" style="position:absolute;left:140px;top:34px;font-size:62px;line-height:1">%</p>
    <p class="bebas c-mid" style="position:absolute;left:140px;top:96px;font-size:50px;line-height:1">OFF</p>
    <p class="t bebas c-white" style="top:142px;font-size:52px">EVERYTHING</p>
    <div style="position:absolute;left:23px;top:183px;width:176px;height:29px;background:var(--pink)"></div>
    <p class="t script c-wine" style="top:184px;font-size:25px">Mother's Day</p>
    <p class="t bebas c-white" style="top:214px;font-size:32px">SPRING DETOX SALE</p>
  </section>

  <!-- Tile 6 -->
  <section class="tile" style="left:27px;top:307px;background:var(--white)">
    <div class="photo" role="img" aria-label="Faded supplement bottle backdrop" style="left:0;top:10px;width:150px;height:200px;opacity:.5"></div>
    <p class="t bebas c-mid" style="top:16px;font-size:68px">25% OFF</p>
    <p class="t script c-wine" style="top:62px;font-size:34px">Mother's Day</p>
    <p class="t anton c-wine" style="top:88px;font-size:110px;letter-spacing:-2px">SALE</p>
    <p class="script c-mid" style="position:absolute;left:12px;top:190px;font-size:54px;line-height:1">Feel</p>
    <p class="bebas c-wine" style="position:absolute;left:14px;top:246px;font-size:24px;line-height:1">AMAZING AGAIN</p>
    <div class="photo" role="img" aria-label="Woman standing behind supplement bottles" style="left:150px;top:148px;width:74px;height:132px;background:linear-gradient(180deg,#e6d3db,#c7aab6)"></div>
  </section>

  <!-- Tile 7 -->
  <section class="tile" style="left:258px;top:307px">
    <p class="anton c-pink" style="position:absolute;left:28px;top:18px;font-size:120px;line-height:1">25</p>
    <p class="bebas c-pink" style="position:absolute;left:142px;top:28px;font-size:62px;line-height:1">%</p>
    <p class="bebas c-white" style="position:absolute;left:140px;top:78px;font-size:56px;line-height:1">OFF</p>
    <p class="t script c-pink" style="top:124px;font-size:44px">Mother's</p>
    <p class="t spaced c-white" style="top:170px;font-size:14px">DAY SALE</p>
    <p class="t script c-pink" style="top:188px;font-size:48px">Refresh</p>
    <p class="t spaced c-white" style="top:244px;font-size:14px">YOUR BODY</p>
  </section>

  <!-- Tile 8 -->
  <section class="tile tile--blush" style="left:488px;top:307px">
    <svg style="position:absolute;left:20px;top:14px" width="92" height="34" viewBox="0 0 92 34"><path d="M0 4 L80 0 L92 16 L80 30 L0 34Z" fill="#8f2160"/></svg>
    <p class="bebas c-white" style="position:absolute;left:26px;top:17px;font-size:28px;line-height:1">25% OFF</p>
    <div class="photo" role="img" aria-label="Four small supplement bottles" style="left:116px;top:12px;width:88px;height:34px"></div>
    <p class="t anton c-plum" style="top:44px;font-size:66px">SPRING</p>
    <p class="t script c-plum" style="top:106px;font-size:36px">Detox Sale</p>
    <p class="t bebas c-mid" style="top:141px;font-size:50px">THIS SPRING</p>
    <p class="t script c-wine" style="top:180px;font-size:36px">Shine This</p>
    <p class="t anton c-plum" style="top:214px;font-size:56px">SUMMER</p>
  </section>

  <!-- Tile 9 -->
  <section class="tile" style="left:718px;top:307px">
    <svg class="white-curve" width="224" height="120" viewBox="0 0 224 120" style="height:120px"><path d="M0 42 Q112 0 224 42 V120 H0Z" fill="#fff"/></svg>
    <p class="t italic c-white" style="top:20px;font-size:34px">25% Off</p>
    <p class="t brush c-white" style="top:54px;font-size:44px">Mother's</p>
    <p class="t italic c-white" style="top:96px;font-size:34px">Day Sale</p>
    <div style="position:absolute;left:36px;top:139px;width:152px;height:34px;background:var(--white);border-radius:8px"></div>
    <p class="t italic c-plum" style="top:143px;font-size:13px;letter-spacing:0">Detox this Summer</p>
    <p class="t italic c-plum" style="top:158px;font-size:13px;letter-spacing:0">Shine this Summer</p>
    <div class="photo" role="img" aria-label="Four supplement bottles in a row" style="left:20px;top:180px;width:186px;height:86px"></div>
  </section>

  <!-- Tile 10 -->
  <section class="tile" style="left:948px;top:307px">
    <div class="photo" role="img" aria-label="Faded row of supplement bottles" style="left:6px;top:190px;width:212px;height:86px;background:#9d3a70;opacity:.6"></div>
    <p class="t bebas c-white" style="top:28px;font-size:62px">25% OFF</p>
    <p class="t script c-white" style="top:76px;font-size:21px">Mother's Day Sale</p>
    <div style="position:absolute;left:20px;top:106px;width:184px;height:27px;background:var(--white)"></div>
    <p class="t bebas c-plum" style="top:107px;font-size:29px">SPRING DETOX FOR A</p>
    <p class="t anton c-pink" style="top:134px;font-size:58px">SUMMER</p>
    <p class="t brush c-white" style="top:186px;font-size:70px">BODY</p>
  </section>

</main>
</body>
</html>
```